Standardization and redesign of graphics for a non-fiction book

For a book project, 11 graphics need to be visually unified so that all the graphics in the book are in the same style. The graphics must be created from scratch. Just new colors aren't enough. Some of the existing graphics are by other authors who own the copyright. Accordingly, the new graphics must be truly new. This is especially true for the "2 S-curves" graphic.

Target Market(s)

Manager Furniture Industry

Industry/Entity Type

Möbel

Colors
0054AA
0677BA
7BADD7
CADEEF
E8F1F8

```html
<!DOCTYPE html>
<html lang="de">
<head>
<meta charset="utf-8">
<title>Geschäftsmodell-Dreieck</title>
<link rel="stylesheet" href="https://fonts.googleapis.com/css2?family=Poppins:wght@600;700&display=swap">
<style>
  :root {
    --bg: #ffffff;
    --navy: #0054AA;
    --blue: #0677BA;
    --sky: #7BADD7;
    --mist: #CADEEF;
    --ice: #E8F1F8;
    --label: #0054AA;
    --question: #3d5a78;
    --segment-text: #ffffff;
    --divider: #ffffff;
  }
  html, body {
    margin: 0;
    padding: 0;
    width: 1200px;
    height: 1200px;
    overflow: hidden;
    background: var(--bg);
  }
  .diagram {
    display: block;
    width: 1200px;
    height: 1200px;
    font-family: "Poppins", sans-serif;
  }
  .segment-top { fill: var(--navy); }
  .segment-left { fill: var(--blue); }
  .segment-right { fill: var(--sky); }
  .question { fill: var(--question); font-weight: 600; font-size: 22px; }
  .node-ring { fill: var(--bg); stroke: var(--blue); stroke-width: 4; }
  .node-inner { fill: var(--ice); stroke: var(--mist); stroke-width: 2; }
  .node-center { fill: var(--ice); stroke: var(--bg); stroke-width: 6; }
  .node-label { fill: var(--label); font-weight: 700; font-size: 30px; }
  .segment-label { fill: var(--segment-text); font-weight: 700; font-size: 28px; }
  .segment-label.on-light { fill: var(--navy); }
  .divider { stroke: var(--divider); stroke-width: 4; }
</style>
</head>
<body>
<svg class="diagram" viewBox="0 0 1500 1500" xmlns="http://www.w3.org/2000/svg" role="img" aria-label="Geschäftsmodell-Dreieck mit den Fragen Wer, Was, Wie und Wert">

  <!-- Triangle segments -->
  <polygon class="segment-top" points="734,446 921,752 734,861 547,752"/>
  <polygon class="segment-left" points="547,752 330,1107 734,1107 734,861"/>
  <polygon class="segment-right" points="921,752 1138,1107 734,1107 734,861"/>

  <!-- Segment dividers -->
  <line class="divider" x1="547" y1="752" x2="734" y2="861"/>
  <line class="divider" x1="921" y1="752" x2="734" y2="861"/>
  <line class="divider" x1="734" y1="861" x2="734" y2="1107"/>

  <!-- Segment labels -->
  <text class="segment-label" text-anchor="middle">
    <tspan x="734" y="682">Nutzenver-</tspan>
    <tspan x="734" y="713">sprechen</tspan>
  </text>
  <text class="segment-label" text-anchor="middle">
    <tspan x="568" y="973">Ertrags-</tspan>
    <tspan x="568" y="1004">mechanik</tspan>
  </text>
  <text class="segment-label on-light" text-anchor="middle">
    <tspan x="891" y="965">Wert-</tspan>
    <tspan x="891" y="996">schöpfungs-</tspan>
    <tspan x="891" y="1027">kette</tspan>
  </text>

  <!-- Center node -->
  <circle class="node-center" cx="734" cy="861" r="84"/>
  <text class="node-label" x="734" y="872" text-anchor="middle">Wer?</text>

  <!-- Corner nodes -->
  <circle class="node-ring" cx="734" cy="480" r="84"/>
  <circle class="node-inner" cx="734" cy="480" r="70"/>
  <text class="node-label" x="734" y="491" text-anchor="middle">Was?</text>

  <circle class="node-ring" cx="343" cy="1093" r="84"/>
  <circle class="node-inner" cx="343" cy="1093" r="70"/>
  <text class="node-label" x="343" y="1104" text-anchor="middle">Wert?</text>

  <circle class="node-ring" cx="1125" cy="1093" r="84"/>
  <circle class="node-inner" cx="1125" cy="1093" r="70"/>
  <text class="node-label" x="1125" y="1104" text-anchor="middle">Wie?</text>

  <!-- Guiding questions -->
  <text class="question" text-anchor="middle">
    <tspan x="734" y="323">Was bieten wir dem</tspan>
    <tspan x="734" y="356">Kunden an?</tspan>
  </text>
  <text class="question" text-anchor="middle">
    <tspan x="293" y="954">Wie wird Wert</tspan>
    <tspan x="293" y="987">erzielt?</tspan>
  </text>
  <text class="question" text-anchor="middle">
    <tspan x="1182" y="954">Wie stellen wir die</tspan>
    <tspan x="1182" y="987">Leistung her?</tspan>
  </text>
  <text class="question" text-anchor="middle">
    <tspan x="724" y="1162">Wer sind unsere</tspan>
    <tspan x="724" y="1195">Zielkunden?</tspan>
  </text>
</svg>
</body>
</html>
```